Company growth chart/Vision for the next 10 years of growth

I need to show an illustration how the company will grow over the next 10 years. Develop graphic to communicate:

In the center / or main focus ar...

Target Market(s)

Employees in corporate / need to show a future vision to get everyone excited about. Not a growth "tree".

Industry/Entity Type

It Company

Requirements
Must have
• Be an illustration/graphic showing what the project description states.
Nice to have
• I've looked at gears/mountains/icons to showcase this vision and I haven't been able to come up with anything.
Should not have
• A growth tree. Not what I'm looking for. This is corporate.

```html
<!DOCTYPE html>
<html lang="en">
<head>
<meta charset="UTF-8">
<title>Company Growth Vision 2026</title>
<link rel="stylesheet" href="https://fonts.googleapis.com/css2?family=Noto+Serif:wght@400;700&family=Open+Sans:wght@400;600;700&display=swap">
<style>
  :root {
    --bg: #3273b8;
    --bg-deep: #245f9f;
    --yellow: #f7e01a;
    --white: #ffffff;
    --ink-blue: #1f5fa8;
    --grey-text: #8a8d92;
    --disk: #1d5aa5;
  }
  * { margin: 0; padding: 0; box-sizing: border-box; }
  html, body { width: 1135px; height: 1200px; overflow: hidden; }
  body {
    position: relative;
    background: radial-gradient(circle at 50% 45%, #3a7fc6 0%, var(--bg) 55%, var(--bg-deep) 100%);
    font-family: "Open Sans", Arial, sans-serif;
    color: var(--white);
  }
  .gear-art { position: absolute; inset: 0; }
  .title {
    position: absolute; top: 30px; left: 0; width: 100%;
    text-align: center;
    font-family: "Noto Serif", Georgia, serif;
    font-weight: 700; font-size: 33px;
    color: var(--yellow);
  }
  .label { color: var(--yellow); font-weight: 700; font-size: 17px; position: absolute; }
  .note { position: absolute; font-size: 17px; line-height: 24px; }
  .list { position: absolute; list-style: none; font-size: 17px; line-height: 24px; }
  .list li { position: relative; padding-left: 24px; }
  .list li::before {
    content: ""; position: absolute; left: 2px; top: 7px;
    width: 10px; height: 10px; border-radius: 50%;
    border: 2px solid var(--white);
    background: radial-gradient(circle, var(--white) 0 2px, transparent 2.5px);
  }
  .team-copy { left: 689px; top: 126px; width: 330px; }
  .team-bullet { left: 666px; top: 200px; width: 370px; }
  .team-bullet b { color: var(--yellow); }
  .stats { left: 826px; top: 690px; }
  .stats li { line-height: 22px; }
  .stats .value {
    display: block; color: var(--yellow);
    font-family: "Noto Serif", Georgia, serif; font-weight: 700;
    font-size: 24px; line-height: 34px; margin-left: -24px;
  }
  .vision {
    position: absolute; left: 434px; top: 512px; width: 272px;
    text-align: center; font-family: "Noto Serif", Georgia, serif;
    line-height: 1;
  }
  .vision .word { font-size: 42px; font-weight: 700; color: var(--grey-text); }
  .vision .years { font-size: 56px; font-weight: 700; color: var(--ink-blue); margin-top: 6px; }
  .vision .caption { font-size: 23px; color: #1d2a3a; margin-top: 6px; }
  .vision .caption.caps { letter-spacing: 0.5px; margin-top: 10px; }
  .vision .year { font-size: 52px; font-weight: 700; color: var(--ink-blue); margin-top: 8px; }
  .count { font-family: "Open Sans", Arial, sans-serif; font-weight: 700; font-size: 15px; fill: var(--white); }
</style>
</head>
<body>
<svg class="gear-art" width="1135" height="1200" viewBox="0 0 1135 1200">
  <defs>
    <radialGradient id="steel" cx="40%" cy="35%" r="75%">
      <stop offset="0" stop-color="#f4f5f6"/>
      <stop offset="0.6" stop-color="#d2d4d7"/>
      <stop offset="1" stop-color="#9ea2a7"/>
    </radialGradient>
    <radialGradient id="face" cx="50%" cy="45%" r="60%">
      <stop offset="0" stop-color="#fbfbfb"/>
      <stop offset="1" stop-color="#d9dadc"/>
    </radialGradient>
    <linearGradient id="suit" x1="0" y1="0" x2="0" y2="1">
      <stop offset="0" stop-color="#f1c9a5"/>
      <stop offset="0.3" stop-color="#2b3a55"/>
      <stop offset="1" stop-color="#1a2438"/>
    </linearGradient>
    <radialGradient id="crowd-small" cx="50%" cy="50%" r="60%">
      <stop offset="0" stop-color="#ffffff"/>
      <stop offset="1" stop-color="#c9d3e0"/>
    </radialGradient>
    <radialGradient id="crowd-large" cx="50%" cy="50%" r="60%">
      <stop offset="0" stop-color="#ffe23a"/>
      <stop offset="1" stop-color="#e0b400"/>
    </radialGradient>
    <linearGradient id="tower" x1="0" y1="0" x2="1" y2="0">
      <stop offset="0" stop-color="#ffffff"/>
      <stop offset="1" stop-color="#cfd6de"/>
    </linearGradient>
    <linearGradient id="brick" x1="0" y1="0" x2="1" y2="0">
      <stop offset="0" stop-color="#e0443a"/>
      <stop offset="1" stop-color="#b8302a"/>
    </linearGradient>
    <linearGradient id="shopfront" x1="0" y1="0" x2="0" y2="1">
      <stop offset="0" stop-color="#e9dccb"/>
      <stop offset="1" stop-color="#c9b59c"/>
    </linearGradient>
  </defs>

  <g class="backdrop-gears" fill="none" stroke="#2a68ab" opacity="0.55">
    <circle cx="180" cy="240" r="150" stroke-width="30" pathLength="40" stroke-dasharray="1 1"/>
    <circle cx="180" cy="240" r="110" stroke-width="50"/>
    <circle cx="1020" cy="560" r="170" stroke-width="34" pathLength="44" stroke-dasharray="1 1"/>
    <circle cx="1020" cy="560" r="125" stroke-width="55"/>
    <circle cx="360" cy="1140" r="130" stroke-width="28" pathLength="36" stroke-dasharray="1 1"/>
    <circle cx="900" cy="1080" r="120" stroke-width="28" pathLength="34" stroke-dasharray="1 1"/>
  </g>

  <g class="connectors" stroke="#ffffff" stroke-width="3">
    <polyline points="132,201 170,228 300,236" fill="none"/>
    <circle cx="132" cy="201" r="7" fill="none"/>
    <polyline points="706,294 706,340 795,395" fill="none"/>
    <circle cx="706" cy="294" r="7" fill="none"/>
    <polyline points="43,538 43,615 100,650" fill="none"/>
    <circle cx="43" cy="538" r="7" fill="none"/>
    <polyline points="800,643 925,650 945,674" fill="none"/>
    <circle cx="945" cy="674" r="7" fill="none"/>
    <polyline points="339,1005 372,1012 510,1012" fill="none"/>
    <circle cx="339" cy="1005" r="7" fill="none"/>
  </g>

  <!-- personal development gear -->
  <g class="gear gear-personal">
    <circle cx="428" cy="258" r="152" fill="none" stroke="#b9bcc0" stroke-width="26" pathLength="48" stroke-dasharray="1 1"/>
    <circle cx="428" cy="258" r="142" fill="url(#steel)"/>
    <circle cx="428" cy="258" r="108" fill="#ffffff"/>
    <circle cx="428" cy="258" r="98" fill="var(--disk)"/>
    <g class="growth-bars">
      <rect x="362" y="305" width="24" height="28" fill="#f26522"/>
      <rect x="393" y="268" width="24" height="65" fill="#fdb813"/>
      <rect x="424" y="250" width="24" height="83" fill="#f5a800"/>
      <rect x="455" y="254" width="24" height="79" fill="#8dc63f"/>
    </g>
    <g class="growth-arrow" stroke="#ffffff" stroke-width="5" fill="#ffffff">
      <line x1="335" y1="294" x2="420" y2="226"/>
      <polygon points="432,217 410,222 420,235" stroke="none"/>
    </g>
    <rect class="figure-area" x="438" y="170" width="30" height="82" rx="12" fill="url(#suit)" role="img" aria-label="Illustration of a businessman celebrating on top of the tallest bar"/>
  </g>

  <!-- team growth gear -->
  <g class="gear gear-team">
    <circle cx="940" cy="452" r="152" fill="none" stroke="#b9bcc0" stroke-width="26" pathLength="48" stroke-dasharray="1 1"/>
    <circle cx="940" cy="452" r="142" fill="url(#steel)"/>
    <circle cx="940" cy="452" r="108" fill="#ffffff"/>
    <circle cx="940" cy="452" r="98" fill="var(--disk)"/>
    <rect x="867" y="372" width="38" height="52" rx="10" fill="url(#crowd-small)" role="img" aria-label="Illustration of a small team of 20 people"/>
    <rect x="902" y="378" width="126" height="136" rx="34" fill="url(#crowd-large)" role="img" aria-label="Illustration of a large team of 100 people"/>
    <path d="M905,372 Q952,340 998,372" fill="none" stroke="#ffffff" stroke-width="5"/>
    <polygon points="1010,382 990,380 1002,364" fill="#ffffff"/>
    <text class="count" x="875" y="444">20</text>
    <text class="count" x="960" y="533">100</text>
  </g>

  <!-- vertical market gear -->
  <g class="gear gear-vertical">
    <circle cx="180" cy="755" r="156" fill="none" stroke="#b9bcc0" stroke-width="28" pathLength="48" stroke-dasharray="1 1"/>
    <circle cx="180" cy="755" r="146" fill="url(#steel)"/>
    <circle cx="180" cy="755" r="110" fill="#ffffff"/>
    <circle cx="180" cy="755" r="100" fill="var(--disk)"/>
    <g class="buildings" role="img" aria-label="Illustration of a hotel tower with a restaurant and a retail shop">
      <rect x="170" y="675" width="80" height="158" fill="url(#tower)"/>
      <rect x="180" y="665" width="60" height="14" fill="#d9342b"/>
      <rect x="120" y="768" width="76" height="65" fill="url(#shopfront)"/>
      <rect x="240" y="790" width="50" height="43" fill="url(#brick)"/>
    </g>
  </g>

  <!-- regional market gear -->
  <g class="gear gear-regional">
    <circle cx="653" cy="1010" r="146" fill="none" stroke="#b9bcc0" stroke-width="26" pathLength="46" stroke-dasharray="1 1"/>
    <circle cx="653" cy="1010" r="136" fill="url(#steel)"/>
    <circle cx="653" cy="1010" r="104" fill="#ffffff"/>
    <circle cx="653" cy="1010" r="94" fill="var(--disk)"/>
    <g class="buildings" role="img" aria-label="Illustration of a city block with hospital, hotel, office and retail buildings">
      <rect x="551" y="985" width="82" height="70" fill="url(#tower)"/>
      <rect x="633" y="950" width="70" height="105" fill="url(#tower)"/>
      <rect x="645" y="940" width="40" height="12" fill="#d9342b"/>
      <rect x="703" y="968" width="46" height="87" fill="url(#brick)"/>
      <rect x="600" y="1030" width="60" height="25" fill="url(#shopfront)"/>
    </g>
  </g>

  <!-- central vision gear -->
  <g class="gear gear-vision">
    <circle cx="570" cy="630" r="200" fill="none" stroke="#b9bcc0" stroke-width="34" pathLength="60" stroke-dasharray="1 1"/>
    <circle cx="570" cy="630" r="188" fill="url(#steel)"/>
    <circle cx="570" cy="630" r="146" fill="#c4c7cb"/>
    <circle cx="570" cy="630" r="140" fill="url(#face)"/>
    <circle cx="570" cy="630" r="128" fill="none" stroke="#9a9ea3" stroke-width="2.5" stroke-dasharray="8 6"/>
  </g>
</svg>

<h1 class="title">Company growth chart/Vision for the next 10 years of growth</h1>

<div class="label" style="left:641px; top:98px;">Team Growth</div>
<p class="note team-copy">Amount of growth we are projecting and what it really looks like</p>
<ul class="list team-bullet">
  <li>Impact it will have on current team members ( current team is <b>20</b> people . Future growth is <b>100</b> people)</li>
</ul>

<div class="label" style="left:40px; top:160px;">Personal Development</div>

<div class="label" style="left:43px; top:455px;">Vertical Market Focus</div>
<ul class="list" style="left:79px; top:479px;">
  <li>Hotels</li>
  <li>Trade Labor Subcontracting</li>
  <li>Specialty Retail</li>
  <li>Quick Service Restaurants</li>
</ul>

<div class="vision">
  <div class="word">VISION</div>
  <div class="years">10</div>
  <div class="caption">year target</div>
  <div class="caption caps">FUTURE DATE:</div>
  <div class="year">2026</div>
</div>

<ul class="list stats">
  <li>Building Square Footage Impact:<span class="value">500,000 SF</span></li>
  <li>Employee engagement rating:<span class="value">90%</span></li>
  <li>Customer satisfaction rating:<span class="value">95%</span></li>
  <li>Safety EMR at or below:<span class="value">0.65</span></li>
  <li>Employees:<span class="value">160</span></li>
</ul>

<div class="label" style="left:155px; top:957px;">Current Regional Market Focus</div>
<ul class="list" style="left:158px; top:985px;">
  <li>Hotels</li>
  <li>Manufacturing</li>
  <li>Retail</li>
  <li>Office</li>
  <li>Sr. Housing</li>
  <li>Hospitals</li>
</ul>
</body>
</html>
```